SkyvornQ Business Cards and Stationary Design

Need a design for our business cards and stationary. I want to carry on the theme of the logo. I want the business cards to have a design on the back. I would like the business cards and the stationary to carry the same theme, design scheme, and branding

Target Market(s)

Airlines and Maintenance Facilities

Industry/Entity Type

Aviation

Contact Information for Business Card

Name
Position Title
Address: 4827 Trellis Hollow Road, Fort Pierce, Florida, 34951
Office Number
Mobile Number
Email
Website

Font styles to use
Serif
Sans Serif

Colors

Designer to choose colors to be used in the design.

```html
<!DOCTYPE html>
<html lang="en">
<head>
<meta charset="utf-8">
<title>SkyvornQ Business Card</title>
<link rel="stylesheet" href="https://fonts.googleapis.com/css2?family=Montserrat:wght@700&family=Open+Sans:wght@400;600&display=swap">
<style>
  :root {
    --navy: #0b2a57;
    --navy-deep: #082247;
    --sky: #1a8fd6;
    --sky-mid: #1560ad;
    --paper: #ffffff;
    --backdrop: #5a2a12;
    --ink-light: #e8eef7;
  }
  * { margin: 0; padding: 0; box-sizing: border-box; }
  html, body { width: 1200px; height: 872px; overflow: hidden; }
  body {
    background: var(--backdrop);
    font-family: "Open Sans", Arial, sans-serif;
    position: relative;
  }
  .card {
    position: absolute;
    left: 250px;
    width: 700px;
    height: 400px;
    background: var(--paper);
    overflow: hidden;
    box-shadow: 0 6px 18px rgba(0,0,0,.35);
  }
  .card--back { top: 24px; }
  .card--front { top: 448px; }

  .brand-circle {
    position: absolute;
    border-radius: 50%;
    border: 10px solid var(--sky-mid);
  }
  .brand-name {
    position: absolute;
    font-family: "Montserrat", Arial, sans-serif;
    font-weight: 700;
    color: var(--navy);
    letter-spacing: .22em;
    white-space: nowrap;
  }

  /* back side */
  .card--back .brand-circle { left: 120px; top: 120px; width: 160px; height: 160px; }
  .card--back .brand-name { left: 320px; top: 160px; font-size: 40px; }
  .card--back .brand-web {
    position: absolute; left: 324px; top: 218px;
    font-size: 15px; letter-spacing: .28em; color: #333;
  }

  /* front side */
  .front-panel { position: absolute; inset: 0; }
  .card--front .brand-circle { left: 152px; top: 120px; width: 96px; height: 96px; border-width: 7px; }
  .card--front .brand-name { left: 60px; top: 240px; font-size: 38px; }

  .contact {
    position: absolute; right: 44px; top: 52px;
    text-align: right; color: var(--ink-light);
  }
  .contact__name { font-weight: 600; font-size: 24px; color: #fff; letter-spacing: .01em; }
  .contact__title { font-size: 20px; margin-bottom: 26px; }
  .contact__line { font-size: 16px; line-height: 26px; display: flex; justify-content: flex-end; align-items: center; gap: 8px; }
  .contact__line svg { width: 15px; height: 15px; flex: none; }
  .contact__gap { height: 14px; }
</style>
</head>
<body>

<section class="card card--back" aria-label="Card back">
  <div class="brand-circle"></div>
  <div class="brand-name">SKYVORNQ</div>
  <div class="brand-web">www.skyvornq.com</div>
</section>

<section class="card card--front" aria-label="Card front">
  <svg class="front-panel" viewBox="0 0 700 400" width="700" height="400">
    <defs>
      <linearGradient id="edgeBand" x1="0" y1="0" x2="1" y2="1">
        <stop offset="0" stop-color="#1fa3e6"/>
        <stop offset="1" stop-color="#13509f"/>
      </linearGradient>
    </defs>
    <path d="M220,0 H700 V400 H560 C450,330 390,110 220,0 Z" fill="var(--navy)"/>
    <path d="M220,0 C390,110 450,330 560,400" fill="none" stroke="url(#edgeBand)" stroke-width="34"/>
  </svg>

  <div class="brand-circle"></div>
  <div class="brand-name">SKYVORNQ</div>

  <div class="contact">
    <div class="contact__name">DARREN HOLLOWAY</div>
    <div class="contact__title">PRESIDENT</div>
    <div class="contact__line">
      <svg viewBox="0 0 16 16"><circle cx="8" cy="8" r="7" fill="none" stroke="currentColor" stroke-width="1.3"/><path d="M5.5 4.5l1.5 1.5-1 1c.6 1.2 1.5 2.1 2.7 2.7l1-1 1.5 1.5-1 1.2C7.5 11 5 8.5 4.6 5.6z" fill="currentColor"/></svg>
      <span>012-345-6789</span>
    </div>
    <div class="contact__line">
      <svg viewBox="0 0 16 16"><circle cx="8" cy="8" r="7" fill="none" stroke="currentColor" stroke-width="1.3"/><rect x="5.5" y="4" width="5" height="8" rx="1" fill="none" stroke="currentColor" stroke-width="1.2"/></svg>
      <span>012-345-6789</span>
    </div>
    <div class="contact__line">
      <svg viewBox="0 0 16 16"><circle cx="8" cy="8" r="7" fill="none" stroke="currentColor" stroke-width="1.3"/><rect x="4.5" y="5.5" width="7" height="5" fill="none" stroke="currentColor" stroke-width="1.1"/><path d="M4.5 5.5L8 8.3l3.5-2.8" fill="none" stroke="currentColor" stroke-width="1.1"/></svg>
      <span>info@skyvornq.com</span>
    </div>
    <div class="contact__line">
      <svg viewBox="0 0 16 16"><circle cx="8" cy="8" r="7" fill="none" stroke="currentColor" stroke-width="1.3"/><ellipse cx="8" cy="8" rx="3" ry="7" fill="none" stroke="currentColor" stroke-width="1.1"/><path d="M1 8h14" stroke="currentColor" stroke-width="1.1"/></svg>
      <span>www.skyvornq.com</span>
    </div>
    <div class="contact__gap"></div>
    <div class="contact__line">
      <svg viewBox="0 0 16 16"><circle cx="8" cy="8" r="7" fill="none" stroke="currentColor" stroke-width="1.3"/><path d="M8 12.5S5 9.3 5 7a3 3 0 016 0c0 2.3-3 5.5-3 5.5z" fill="none" stroke="currentColor" stroke-width="1.1"/><circle cx="8" cy="7" r="1" fill="currentColor"/></svg>
      <span>Street Name, City Name</span>
    </div>
    <div class="contact__line"><span>Zipcode-012345</span></div>
  </div>
</section>

</body>
</html>
```